Human Resource Consulting practice needs a business card design

We need a business card design (double sided colour) for our Human Resource (HR) consulting practice in regional New South Wales, australia. Our business name is Staff Compass. We support small and medium business across the Mid North Coast of New South Wales by providing them with outsourced HR support, services and products to help them achieve compliance with workplace legislation and across all areas of the employment lifecycle from recruitment to termination and everything in between. Our corporate colours are hot pink and black. The final design should communicate professionalism, trust, people focus.
I have attached the current (old) business card for your reference.

Target Market(s)

Business owners and high level managers

Industry/Entity Type

Business

Contact Information for Business Card

Name
Title
Phone no
Mobile no
Address
PO Box
email address
website

Colors
e34197

Requirements
Must have
• Tempate for changing business card personal details including Name, position title, mobile number, email address.
• Keep current logo and colours as per attached
• Logo must be presented in 2 colours or black only not white
Nice to have
• One side logo and graphic only other side logo and personal details
Should not have
• Should not be the same as the current version (attached) but a modern interpretation.
• Does not need a busy reverse side with our list of services as per current version. I feel this is too busy.
• No photos

```html
<!DOCTYPE html>
<html lang="en">
<head>
<meta charset="utf-8">
<title>Staff Compass – Business Card</title>
<link rel="stylesheet" href="https://fonts.googleapis.com/css2?family=Michroma&family=Arimo:wght@400;700&display=swap">
<style>
  :root {
    --pink: #e3189f;
    --pink-soft: #e34197;
    --black: #0b0b0b;
    --ink-grey: #bdbdbd;
    --text-light: #e6e6e6;
    --backdrop: #ebe7e2;
  }
  html, body {
    margin: 0;
    width: 1200px;
    height: 892px;
    overflow: hidden;
    background: var(--backdrop);
  }
  .sheet {
    position: relative;
    width: 1200px;
    height: 892px;
    display: flex;
    justify-content: center;
    align-items: center;
    gap: 120px;
  }
  .card {
    position: relative;
    width: 360px;
    height: 580px;
    border-radius: 22px;
    background: var(--black);
    overflow: hidden;
    box-shadow: 0 10px 28px rgba(0,0,0,0.18);
  }
  .band {
    position: absolute;
    left: 0;
    right: 0;
    background: var(--pink);
  }
  .band--top { top: 0; height: 64px; }
  .band--bottom { bottom: 0; height: 82px; }

  .wordmark {
    font-family: "Michroma", sans-serif;
    font-weight: 400;
    letter-spacing: 0.5px;
    line-height: 1.15;
    display: flex;
    align-items: center;
    gap: 10px;
    color: var(--pink);
  }
  .wordmark__dot {
    width: 10px;
    height: 10px;
    flex: none;
    background: var(--pink);
  }

  /* Front side: logo and personal details */
  .card--front .wordmark {
    position: absolute;
    left: 40px;
    top: 96px;
    font-size: 30px;
  }

  .person {
    position: absolute;
    left: 40px;
    top: 228px;
  }
  .person__name {
    font-family: "Michroma", sans-serif;
    font-size: 24px;
    font-weight: 400;
    color: var(--pink);
    margin: 0;
    letter-spacing: 1px;
    line-height: 1.2;
  }
  .person__title {
    font-family: "Arimo", sans-serif;
    font-size: 11px;
    letter-spacing: 1.2px;
    color: var(--ink-grey);
    text-transform: uppercase;
    margin: 4px 0 0;
  }

  .contact {
    position: absolute;
    left: 40px;
    top: 306px;
    margin: 0;
    padding: 0;
    list-style: none;
    font-family: "Arimo", sans-serif;
    font-size: 15px;
    color: var(--text-light);
    letter-spacing: 0.6px;
  }
  .contact__item {
    display: flex;
    align-items: center;
    gap: 10px;
    height: 22px;
  }
  .contact__icon {
    width: 16px;
    height: 16px;
    flex: none;
  }
  .contact__address {
    margin: 6px 0 0;
    font-family: "Arimo", sans-serif;
    font-size: 15px;
    line-height: 1.35;
    color: var(--text-light);
    letter-spacing: 0.6px;
  }

  /* Back side: logo only */
  .card--back .wordmark {
    position: absolute;
    left: 0;
    right: 0;
    top: 262px;
    justify-content: center;
    font-size: 30px;
  }
</style>
</head>
<body>
<main class="sheet">

  <section class="card card--front" aria-label="Card front">
    <div class="band band--top"></div>

    <div class="wordmark"><span class="wordmark__dot"></span><span>Staff<br>Compass</span></div>

    <div class="person">
      <h1 class="person__name">Maren Colby</h1>
      <p class="person__title">Principal Consultant</p>
    </div>

    <ul class="contact">
      <li class="contact__item">
        <svg class="contact__icon" viewBox="0 0 16 16" aria-hidden="true">
          <rect width="16" height="16" rx="2" fill="#e3189f"/>
          <path d="M4 5h8v2H4zM5 7h6l1 5H4z" fill="#0b0b0b"/>
        </svg>
        02 5550 1842
      </li>
      <li class="contact__item">
        <svg class="contact__icon" viewBox="0 0 16 16" aria-hidden="true">
          <rect width="16" height="16" rx="2" fill="#e3189f"/>
          <rect x="5" y="3" width="6" height="10" rx="1" fill="#0b0b0b"/>
          <rect x="6" y="4.5" width="4" height="6" fill="#e3189f"/>
        </svg>
        0400 555 218
      </li>
      <li class="contact__item">
        <svg class="contact__icon" viewBox="0 0 16 16" aria-hidden="true">
          <rect width="16" height="16" rx="2" fill="#e3189f"/>
          <rect x="5" y="3" width="6" height="4" fill="#0b0b0b"/>
          <rect x="3" y="7" width="10" height="5" rx="1" fill="#0b0b0b"/>
        </svg>
        02 5550 1907
      </li>
      <li class="contact__item">
        <svg class="contact__icon" viewBox="0 0 16 16" aria-hidden="true">
          <rect width="16" height="16" rx="2" fill="#e3189f"/>
          <circle cx="8" cy="8" r="4.5" fill="none" stroke="#0b0b0b" stroke-width="1.3"/>
          <path d="M3.5 8h9M8 3.5c-2 2.5-2 6.5 0 9M8 3.5c2 2.5 2 6.5 0 9" fill="none" stroke="#0b0b0b" stroke-width="1"/>
        </svg>
        www.staffcompass.com.au
      </li>
      <li class="contact__item">
        <svg class="contact__icon" viewBox="0 0 16 16" aria-hidden="true">
          <rect width="16" height="16" rx="2" fill="#e3189f"/>
          <rect x="3" y="4.5" width="10" height="7" fill="#0b0b0b"/>
          <path d="M3 4.5l5 4 5-4" fill="none" stroke="#e3189f" stroke-width="1"/>
        </svg>
        maren@staffcompass.com.au
      </li>
      <li>
        <p class="contact__address">PO Box 118, Harbourton,<br>NSW 2400</p>
      </li>
    </ul>

    <div class="band band--bottom"></div>
  </section>

  <section class="card card--back" aria-label="Card back">
    <div class="band band--top"></div>
    <div class="wordmark"><span class="wordmark__dot"></span><span>Staff<br>Compass</span></div>
    <div class="band band--bottom"></div>
  </section>

</main>
</body>
</html>
```